International business needs business cards

Our company, DRV Ventures Inc. is in the business of supplying a range construction products with particular emphasis on CEMENT. We have developed our own brand - TORVAN SUPPLIES - with which to infiltrate the market. We are launching our brand of cement (TORVAN Type IS Cement) into the Caribbean which is unlike anything this market has ever seen. A monopoly has existed here for the past 60-odd years and the market has now opened to allow the importation of other brands and consumers are anxious and ready for change/improvement. We are very excited to be launching and want to make a great first impression. We will be conducting workshops and seminars (from government level to the hardware store owners) and we want our business card to give us the strong, confident introduction that we need.

Target Market(s)

construction; builders; engineers; home owners

Industry/Entity Type

Construction

Contact Information for Business Card

Marisol Depree
CEO
cell # 1 555 4180736
Ground floor,Lindell Plaza Suite 2734
George Town,Grand Cayman
Cayman Islands,KY1-4823
EMAIL: m.depree@drvventuresinc.example
web site drvventuresinc.example

COMPANY: skype info drv.ventures.example

second card
Yvette Brannock-Depree
CFO
CELL# 1 555 607 3941
George Town,Grand Cayman
Cayman Islands,KY1-4823
EMAIL: y.brannockdepree@drvventuresinc.example
website drvventuresinc.example

Requirements
Must have
• Business cards must display BOTH logos - DRV is the company and TORVAN is the brand.

```html
<!DOCTYPE html>
<html lang="en">
<head>
<meta charset="utf-8">
<title>DRV Ventures Inc. – Business Card</title>
<link rel="stylesheet" href="https://fonts.googleapis.com/css2?family=Open+Sans:wght@400;600;700&display=swap">
<style>
  :root {
    --backdrop: #2e2e30;
    --card: #ffffff;
    --ink: #1c1c1c;
    --ink-soft: #3a3a3a;
    --maroon: #8b1c1f;
    --rule: #c9a3a4;
  }
  * { box-sizing: border-box; margin: 0; padding: 0; }
  html, body { width: 1200px; height: 900px; overflow: hidden; }
  body {
    background: var(--backdrop);
    font-family: "Open Sans", Arial, sans-serif;
    color: var(--ink);
    position: relative;
  }
  .card {
    position: absolute;
    width: 700px;
    height: 400px;
    background: var(--card);
    border-radius: 26px;
    box-shadow: 0 10px 30px rgba(0,0,0,.45);
  }
  .card--front { left: 110px; top: 40px; }
  .card--back  { left: 390px; top: 465px; }

  /* Front: brand */
  .brand {
    position: absolute;
    left: 0; right: 0; top: 130px;
    display: flex; align-items: center; justify-content: center; gap: 18px;
  }
  .brand__dot {
    width: 34px; height: 34px; border-radius: 50%;
    background: var(--ink-soft);
  }
  .brand__name {
    font-size: 56px; font-weight: 700; letter-spacing: 6px;
    color: var(--ink-soft);
  }
  .front-web {
    position: absolute; left: 0; right: 0; top: 318px;
    display: flex; align-items: center; justify-content: center; gap: 8px;
    font-size: 19px; color: var(--ink);
  }
  .front-web__dot {
    width: 16px; height: 16px; border-radius: 50%; background: var(--maroon);
  }

  /* Back: company + contact */
  .company {
    position: absolute; left: 60px; top: 250px;
    display: flex; align-items: center; gap: 14px;
  }
  .company__square { width: 84px; height: 84px; background: var(--maroon); }
  .company__name {
    font-size: 27px; font-weight: 700; color: var(--ink); line-height: 1.1;
    width: 170px;
  }
  .divider {
    position: absolute; left: 338px; top: 70px;
    width: 1px; height: 210px; background: var(--rule);
  }
  .contact { position: absolute; left: 358px; top: 62px; }
  .contact__name { font-size: 28px; font-weight: 700; letter-spacing: .5px; }
  .contact__role { font-size: 15px; font-weight: 600; color: var(--maroon); margin-bottom: 8px; }
  .contact__address { font-size: 15px; font-weight: 600; line-height: 1.3; margin-bottom: 6px; }
  .contact__list { list-style: none; font-size: 15px; font-weight: 600; line-height: 1.45; }
  .contact__list li { display: flex; align-items: center; gap: 8px; }
  .contact__list svg { width: 13px; height: 13px; flex: none; }
</style>
</head>
<body>
  <section class="card card--front">
    <div class="brand">
      <span class="brand__dot"></span>
      <span class="brand__name">TORVAN</span>
    </div>
    <div class="front-web">
      <span class="front-web__dot"></span>
      <span>drv.ventures.example</span>
    </div>
  </section>

  <section class="card card--back">
    <div class="company">
      <span class="company__square"></span>
      <span class="company__name">DRV Ventures Inc.</span>
    </div>
    <div class="divider"></div>
    <div class="contact">
      <h1 class="contact__name">MARISOL DEPREE</h1>
      <p class="contact__role">CEO</p>
      <p class="contact__address">Ground floor,Lindell Plaza Suite 2734<br>George Town,Grand Cayman<br>Cayman Islands,KY1-4823</p>
      <ul class="contact__list">
        <li>
          <svg viewBox="0 0 16 16" aria-hidden="true"><path fill="#8b1c1f" d="M3 1l3 3-1.5 2a9 9 0 0 0 5.5 5.5L12 10l3 3-2 2C7 15 1 9 1 3z"/></svg>
          1 555 4180736
        </li>
        <li>
          <svg viewBox="0 0 16 16" aria-hidden="true"><rect x="1.5" y="3.5" width="13" height="9" fill="none" stroke="#8b1c1f" stroke-width="1.6"/><path d="M1.5 3.5L8 9l6.5-5.5" fill="none" stroke="#8b1c1f" stroke-width="1.6"/></svg>
          m.depree@drvventuresinc.example
        </li>
        <li>
          <svg viewBox="0 0 16 16" aria-hidden="true"><circle cx="8" cy="8" r="6.5" fill="none" stroke="#8b1c1f" stroke-width="1.5"/><ellipse cx="8" cy="8" rx="2.8" ry="6.5" fill="none" stroke="#8b1c1f" stroke-width="1.2"/><path d="M1.5 8h13" stroke="#8b1c1f" stroke-width="1.2"/></svg>
          www.drvventuresinc.example
        </li>
      </ul>
    </div>
  </section>
</body>
</html>
```